Building company buisness cards

We are looking for a sharp modern new look for our business cards.We are a New Zealand based company that specialises in house and land packages.We have attached a photo of the current logo and would like to see if it can be improved somehow if needed.We are open to any colours but we have chosen Black and White at this stage. Feel free to change the font and make the logo smarter looking.Play with the colours and see what looks best.We want a card that looks so good know one will want to throw it away!

Target Market(s)

Building profesonals, home buyers

Industry/Entity Type

Building

Contact Information for Business Card

Garrick Tenwood
0275390628
garrickt@hartvale.co.nz

Font styles to use
Serif
Sans Serif

Colors

Designer to choose colors to be used in the design.

Requirements
Must have
• Just the logo on one side and details on the other
• Clean simple looking card
Nice to have
• Round corners and detail like raised or spot UV
• Something that stands out
Should not have
• To title needed, Director etc

```html
<!DOCTYPE html>
<html lang="en">
<head>
<meta charset="UTF-8">
<title>Hartvale Business Card</title>
<link rel="stylesheet" href="https://fonts.googleapis.com/css2?family=Tinos:wght@700&family=Arimo:wght@400&display=swap">
<style>
  :root {
    --backdrop: #e6e2dc;
    --card: #25282c;
    --ink: #ffffff;
    --ink-soft: #e4e6e8;
    --rule: #9a9ea3;
    --ring: #34383d;
    --brand: #c3c7cc;
  }
  * { margin: 0; padding: 0; box-sizing: border-box; }
  html, body {
    width: 1200px;
    height: 780px;
    overflow: hidden;
    background: var(--backdrop);
  }
  .sheet {
    position: relative;
    width: 1200px;
    height: 780px;
    display: flex;
    align-items: center;
    justify-content: center;
    gap: 80px;
  }
  .card {
    position: relative;
    width: 440px;
    height: 440px;
    background: var(--card);
    border-radius: 30px;
    box-shadow: 0 10px 26px rgba(0,0,0,0.22);
    color: var(--ink);
    overflow: hidden;
  }
  /* details side */
  .details {
    display: flex;
    flex-direction: column;
    align-items: center;
    justify-content: center;
  }
  .details__ring {
    position: absolute;
    left: 50%;
    top: 50%;
    width: 360px;
    height: 360px;
    transform: translate(-50%, -50%);
  }
  .details__content {
    position: relative;
    display: flex;
    flex-direction: column;
    align-items: center;
  }
  .details__name {
    font-family: "Tinos", "Times New Roman", serif;
    font-weight: 700;
    font-size: 32px;
    letter-spacing: 1px;
    margin-bottom: 20px;
  }
  .details__icon {
    width: 18px;
    height: 18px;
    margin-bottom: 5px;
  }
  .details__line {
    font-family: "Arimo", Arial, sans-serif;
    font-size: 18px;
    letter-spacing: 1px;
    color: var(--ink-soft);
  }
  .details__rule {
    width: 230px;
    height: 1px;
    background: var(--rule);
    margin: 8px 0 9px;
  }
  /* logo side */
  .brand {
    display: flex;
    align-items: center;
    justify-content: center;
  }
  .brand__name {
    font-family: "Tinos", "Times New Roman", serif;
    font-weight: 700;
    font-size: 52px;
    color: var(--brand);
    letter-spacing: 2px;
  }
</style>
</head>
<body>
<main class="sheet">
  <section class="card details" aria-label="Contact side">
    <svg class="details__ring" viewBox="0 0 360 360" aria-hidden="true">
      <circle cx="180" cy="180" r="170" fill="none" stroke="var(--ring)" stroke-width="12"/>
    </svg>
    <div class="details__content">
      <h1 class="details__name">Garrick Tenwood</h1>
      <svg class="details__icon" viewBox="0 0 20 20" aria-hidden="true">
        <circle cx="10" cy="10" r="9" fill="none" stroke="var(--ink)" stroke-width="1.4"/>
        <rect x="7" y="5" width="6" height="10" rx="1" fill="none" stroke="var(--ink)" stroke-width="1.3"/>
        <line x1="9" y1="13.3" x2="11" y2="13.3" stroke="var(--ink)" stroke-width="1"/>
      </svg>
      <p class="details__line">0275390628</p>
      <div class="details__rule"></div>
      <svg class="details__icon" viewBox="0 0 20 20" aria-hidden="true">
        <circle cx="10" cy="10" r="9" fill="none" stroke="var(--ink)" stroke-width="1.4"/>
        <rect x="5" y="6.5" width="10" height="7" fill="none" stroke="var(--ink)" stroke-width="1.3"/>
        <polyline points="5,6.5 10,10.5 15,6.5" fill="none" stroke="var(--ink)" stroke-width="1.2"/>
      </svg>
      <p class="details__line">garrickt@hartvale.co.nz</p>
    </div>
  </section>

  <section class="card brand" aria-label="Name side">
    <span class="brand__name">Hartvale</span>
  </section>
</main>
</body>
</html>
```